Business Card for Coastal Tundrabridge Advisory

We need a business card for Coastal Tundrabridge Advisory. The company website address is provided below. The company logo is attached. We provide specialized permafrost services to the mining, transportation, and oil & gas industries. The card should be prepared for:
Matthias Korhonen, PhD.
Coastal Tundrabridge Advisory
PO Box 418259
Quillwater, Alaska 99642
Direct: +1-907-555-0143
Email: mkorhonen@tundrabridgeadvisory.example
Website: www.coastaltundrabridgeadvisory.example

```html
<!DOCTYPE html>
<html lang="en">
<head>
<meta charset="utf-8">
<title>Coastal Tundrabridge Advisory – Business Card</title>
<link rel="stylesheet" href="https://fonts.googleapis.com/css2?family=Roboto:ital,wght@0,300;0,400;0,700;1,400&display=swap">
<style>
  :root {
    --backdrop: #222222;
    --paper: #ffffff;
    --ink: #14171f;
    --ink-soft: #2a2d33;
    --rule: #1b1b1b;
  }
  * { box-sizing: border-box; margin: 0; padding: 0; }
  html, body { width: 1200px; height: 780px; overflow: hidden; }
  body {
    background: var(--backdrop);
    font-family: "Roboto", Arial, sans-serif;
    color: var(--ink);
    position: relative;
  }
  .card {
    position: absolute;
    top: 236px;
    width: 540px;
    height: 309px;
    background: var(--paper);
    box-shadow: 0 10px 30px rgba(0,0,0,0.45);
  }
  .card--front { left: 40px; }
  .card--back { left: 620px; }

  /* Front: personal details */
  .person {
    position: absolute;
    left: 24px;
    top: 82px;
    width: 256px;
    text-align: right;
  }
  .person__name {
    font-size: 26px;
    line-height: 1.1;
    white-space: nowrap;
    font-weight: 400;
  }
  .person__given { font-weight: 700; }
  .person__family { font-weight: 300; }
  .person__degree {
    display: block;
    font-weight: 700;
    font-size: 16px;
    margin-top: 2px;
  }
  .divider {
    position: absolute;
    left: 292px;
    top: 96px;
    width: 1px;
    height: 84px;
    background: var(--rule);
  }
  .contact {
    position: absolute;
    left: 304px;
    top: 122px;
    list-style: none;
  }
  .contact__item {
    display: flex;
    align-items: center;
    gap: 6px;
    font-size: 10.5px;
    line-height: 1;
    margin-bottom: 8px;
    white-space: nowrap;
    color: var(--ink-soft);
  }
  .contact__icon { width: 11px; height: 11px; flex: none; }
  .address {
    position: absolute;
    left: 70px;
    top: 228px;
    font-size: 13.5px;
    color: var(--ink-soft);
    white-space: nowrap;
  }

  /* Back: company */
  .company {
    position: absolute;
    left: 0;
    right: 0;
    top: 92px;
    text-align: center;
    font-size: 30px;
    font-weight: 700;
    letter-spacing: 0.5px;
    color: var(--ink);
  }
  .services {
    position: absolute;
    left: 0;
    right: 0;
    top: 210px;
    text-align: center;
  }
  .services__title {
    font-size: 11px;
    font-weight: 700;
    margin-bottom: 4px;
  }
  .services__text {
    font-size: 10.5px;
    font-style: italic;
    color: var(--ink-soft);
  }
</style>
</head>
<body>
  <section class="card card--front" aria-label="Business card front">
    <div class="person">
      <h1 class="person__name"><span class="person__given">Matthias</span> <span class="person__family">Korhonen</span></h1>
      <span class="person__degree">PhD</span>
    </div>
    <div class="divider"></div>
    <ul class="contact">
      <li class="contact__item">
        <svg class="contact__icon" viewBox="0 0 12 12" aria-hidden="true"><circle cx="6" cy="6" r="6" fill="#14171f"/><path d="M4 3.2 L5 3 L5.6 4.6 L4.9 5.1 Q5.5 6.6 6.9 7.1 L7.4 6.4 L9 7 L8.8 8 Q6 8.6 4 5.6 Q3.5 4.2 4 3.2Z" fill="#fff"/></svg>
        <span>+1-907-555-0143</span>
      </li>
      <li class="contact__item">
        <svg class="contact__icon" viewBox="0 0 12 12" aria-hidden="true"><circle cx="6" cy="6" r="6" fill="#14171f"/><rect x="3" y="4" width="6" height="4.2" fill="none" stroke="#fff" stroke-width="0.8"/><path d="M3 4 L6 6.3 L9 4" fill="none" stroke="#fff" stroke-width="0.8"/></svg>
        <span>mkorhonen@tundrabridgeadvisory.example</span>
      </li>
      <li class="contact__item">
        <svg class="contact__icon" viewBox="0 0 12 12" aria-hidden="true"><circle cx="6" cy="6" r="6" fill="#14171f"/><circle cx="6" cy="6" r="3.2" fill="none" stroke="#fff" stroke-width="0.7"/><ellipse cx="6" cy="6" rx="1.4" ry="3.2" fill="none" stroke="#fff" stroke-width="0.7"/><path d="M2.8 6 H9.2" stroke="#fff" stroke-width="0.7"/></svg>
        <span>www.coastaltundrabridgeadvisory.example</span>
      </li>
    </ul>
    <p class="address">PO Box 418259 Quillwater, Alaska 99642</p>
  </section>

  <section class="card card--back" aria-label="Business card back">
    <h2 class="company">Coastal Tundrabridge Advisory</h2>
    <div class="services">
      <p class="services__title">OUR SERVICES</p>
      <p class="services__text">We provide specialized permafrost services to the mining, transportation, and oil &amp; gas industries</p>
    </div>
  </section>
</body>
</html>
```